Finding the Root: Reason in Clinical Choice-Crafting

I'd like a cover that looks like it would fit on the shelf next to "The Illness Mirage" by Corwin Talley, "The Close of Forgetting" by Hugh Marchetti, "Meal Mend" by Paul Grieve, "The Energy Restart Plan" by Oscar Pemberley or "The Gland Restart Plan" by the same or "The Cortex Restart Plan" by the same ... either text only (with some interesting fonts that make the title stand out, and the subtitle smaller) or a relevant image, though I'm not entirely sure what that would be since this is a book about big-picture medical decision making.
Author name is Dr Tessa Morrow, NMD
I'll eventually request an e-book, paperback, and audio cover from the winner...

Target Market(s)

practicing physicians

Industry/Entity Type

medicine

Requirements
Must have
• look similar to other books in the genre

```html
<!DOCTYPE html>
<html lang="en">
<head>
<meta charset="utf-8">
<title>Finding the Root — Book Cover</title>
<link rel="stylesheet" href="https://fonts.googleapis.com/css2?family=Barlow+Condensed:wght@500&family=Libre+Baskerville:wght@400;700&display=swap">
<style>
  :root {
    --backdrop: #dcdcdc;
    --navy: #001b3d;
    --cream: #f5f3f0;
    --gold: #8f7a3a;
    --ink: #0d1d3f;
  }
  html, body {
    margin: 0;
    padding: 0;
    width: 1200px;
    height: 2854px;
    overflow: hidden;
    background: var(--backdrop);
  }
  .book-cover {
    position: absolute;
    left: 60px;
    top: 617px;
    width: 1080px;
    height: 1619px;
    box-shadow: 0 24px 60px rgba(0, 0, 0, 0.28);
  }
  .title-sans {
    font-family: "Barlow Condensed", "Arial Narrow", sans-serif;
    font-weight: 500;
    fill: var(--cream);
  }
  .subtitle-serif {
    font-family: "Libre Baskerville", Georgia, serif;
    fill: var(--ink);
  }
  .subtitle-keyword {
    font-family: "Libre Baskerville", Georgia, serif;
    font-weight: 700;
    fill: var(--gold);
  }
  .rule-light { stroke: var(--cream); stroke-width: 2; }
  .rule-dark { stroke: var(--ink); stroke-width: 1.2; }
</style>
</head>
<body>
  <svg class="book-cover" viewBox="0 0 922 1382" xmlns="http://www.w3.org/2000/svg" aria-label="Book cover: Finding the Root, Reason in Clinical Choice-Crafting, by Dr Tessa Morrow, NMD">
    <rect class="cover-top-band" x="0" y="0" width="922" height="862" fill="var(--navy)"/>
    <rect class="cover-bottom-band" x="0" y="862" width="922" height="520" fill="var(--cream)"/>

    <text class="title-sans title-line-one" x="448" y="265" font-size="250" text-anchor="middle" textLength="675" lengthAdjust="spacingAndGlyphs">FINDING</text>

    <line class="rule-light" x1="117" y1="373" x2="375" y2="373"/>
    <text class="title-sans title-line-two" x="461" y="435" font-size="172" text-anchor="middle" textLength="150" lengthAdjust="spacingAndGlyphs">THE</text>
    <line class="rule-light" x1="547" y1="373" x2="806" y2="373"/>

    <text class="title-sans title-line-three" x="463" y="880" font-size="540" text-anchor="middle" textLength="744" lengthAdjust="spacingAndGlyphs">ROOT</text>

    <line class="rule-dark" x1="120" y1="955" x2="325" y2="955"/>
    <text class="subtitle-serif subtitle-lead" x="461" y="975" font-size="56" text-anchor="middle">Reason in</text>
    <line class="rule-dark" x1="597" y1="955" x2="802" y2="955"/>

    <text class="subtitle-keyword" x="462" y="1130" font-size="142" text-anchor="middle" textLength="710" lengthAdjust="spacingAndGlyphs">CLINICAL</text>

    <text class="subtitle-serif subtitle-tail" x="461" y="1210" font-size="46" text-anchor="middle" textLength="540" lengthAdjust="spacing">Choice-Crafting</text>

    <text class="subtitle-serif author-name" x="461" y="1345" font-size="48" text-anchor="middle" textLength="592" lengthAdjust="spacingAndGlyphs">Dr Tessa Morrow, NMD</text>
  </svg>
</body>
</html>
```